Business Card Design for Training Business

Clear Path Coaching is a new business that delivers training and other services with a focus on topics related to mental health and wellbeing, for example, Wellmind Response Course, Resilience etc. We have a strong focus on evidence-based psychology and neuroscience. I have a logo which I will upload with the brief, so please consider colours that work well with the logo.
Target Market(s)
Adults, workplaces (particularly government and not-for-profits)
Industry/Entity Type
Business
Contact Information for Business Card
Head Strong TrainingSamantha SellwoodDirector0438 770 850sam@headstrongtraining.com.auwww.headstrongtraining.com.au

```html
<!DOCTYPE html>
<html lang="en">
<head>
<meta charset="utf-8">
<title>Clear Path Coaching – Business Card</title>
<link rel="stylesheet" href="https://fonts.googleapis.com/css2?family=Lato:wght@300;400&display=swap">
<style>
  :root {
    --backdrop: #2e2e30;
    --card: #f6f6f6;
    --teal: #1fa9ac;
    --teal-soft: #8fd3d2;
    --ink: #5b5654;
    --ink-soft: #6f6a68;
    --rule: #3a3a3a;
  }
  * { margin: 0; padding: 0; box-sizing: border-box; }
  html, body {
    width: 1200px;
    height: 857px;
    overflow: hidden;
    background: var(--backdrop);
    font-family: "Lato", "Helvetica Neue", Arial, sans-serif;
  }
  .stage {
    width: 1200px;
    height: 857px;
    display: flex;
    align-items: center;
    justify-content: center;
  }
  .card {
    width: 460px;
    height: 740px;
    background: var(--card);
    border-radius: 26px;
    display: flex;
    flex-direction: column;
    align-items: center;
    padding-top: 54px;
    text-align: center;
  }
  .rule {
    height: 1.5px;
    background: var(--rule);
  }
  .rule--top { width: 230px; }
  .rule--bottom { width: 270px; }
  .flourish {
    display: block;
    width: 120px;
    height: 8px;
    border-radius: 4px;
    background: linear-gradient(90deg, transparent, #4a4a4a 30%, #4a4a4a 70%, transparent);
    opacity: 0.75;
    margin: 9px 0;
  }
  .person-name {
    color: var(--teal);
    font-weight: 300;
    font-size: 29px;
    letter-spacing: 0.5px;
    text-transform: uppercase;
    line-height: 1.1;
  }
  .person-role {
    color: var(--ink-soft);
    font-weight: 300;
    font-size: 19px;
    margin-top: 2px;
  }
  .brand {
    margin-top: 30px;
    display: flex;
    flex-direction: column;
    align-items: center;
  }
  .brand-mark {
    width: 168px;
    height: 168px;
  }
  .brand-name {
    margin-top: 28px;
    color: var(--ink);
    font-weight: 300;
    font-size: 36px;
    letter-spacing: 6px;
    line-height: 1.25;
    text-transform: uppercase;
  }
  .contact {
    margin-top: 40px;
    display: flex;
    flex-direction: column;
    align-items: center;
    color: var(--ink);
    font-weight: 300;
    font-size: 23px;
  }
  .dots {
    display: flex;
    gap: 36px;
    margin: 14px 0;
  }
  .dots span {
    width: 13px;
    height: 13px;
    border-radius: 50%;
    background: var(--teal);
  }
</style>
</head>
<body>
<main class="stage">
  <article class="card">
    <div class="rule rule--top"></div>
    <span class="flourish" role="img" aria-label="Decorative scroll flourish"></span>
    <h1 class="person-name">Rebecca Tanfield</h1>
    <p class="person-role">Director</p>
    <span class="flourish" role="img" aria-label="Decorative scroll flourish"></span>
    <div class="rule rule--bottom"></div>

    <section class="brand">
      <svg class="brand-mark" viewBox="0 0 168 168" aria-hidden="true">
        <circle cx="84" cy="84" r="82" fill="var(--teal)"/>
      </svg>
      <h2 class="brand-name">Clear Path<br>Coaching</h2>
    </section>

    <section class="contact">
      <p class="contact-phone">0491 362 517</p>
      <div class="dots"><span></span><span></span><span></span></div>
      <p class="contact-email">bec@clearpathcoaching.example.au</p>
      <div class="dots"><span></span><span></span><span></span></div>
      <p class="contact-web">www.clearpathcoaching.example.au</p>
    </section>
  </article>
</main>
</body>
</html>
```